Stylish Business Cards Wanted

- DOUBLE SIDED Design Required -

High end, edgy cards for a corporate and personal stylist. Must include logo,
Name: Belinda Harwick
Title: Director and Stylist
telephone : +61 8 7142 5809
email: belinda@theloombriefing.example
website: theloombriefing.example
Tag: Corporate Workwear & Uniform Specialist | Personal Stylist
Would like nice icons for telephone, email, website

Target Market(s)

Businesses wanting stylish uniforms, people wanting stylish wardrobes

Industry/Entity Type

Corporate Workwear Stylist

Contact Information for Business Card

I would like black, white and gold foiling incorporated in the design - possibly a touch of the other colours on my branding guide attached Name: Belinda Harwick Title: Director and Stylist telephone : +61 8 7142 5809 email: belinda@theloombriefing.example website: theloombriefing.example Tag: Corporate Workwear & Uniform Specialist | Personal Stylist Would like nice icons for telephone, email, website

Font styles to use
Other font styles liked:
• Raleway

Colors

Designer to choose colors to be used in the design.

Requirements
Must have
• Gold foil accents

```html
<!DOCTYPE html>
<html lang="en">
<head>
<meta charset="utf-8">
<title>The Loom Briefing — Business Cards</title>
<link href="https://fonts.googleapis.com/css2?family=Arimo:wght@400;700&family=Courgette&display=swap" rel="stylesheet">
<style>
  :root {
    --backdrop: #1c1c1d;
    --card: #0b0b0b;
    --card-edge: #262626;
    --ink: #f1f1f1;
    --silver: #cfd2d2;
    --gold: #e3b340;
    --rule: #3a3a3a;
  }
  * { margin: 0; padding: 0; box-sizing: border-box; }
  html, body {
    width: 1200px; height: 900px; overflow: hidden;
    background: var(--backdrop);
  }
  .sheet {
    width: 1200px; height: 900px;
    display: flex; align-items: center; justify-content: center; gap: 40px;
  }
  .card {
    width: 540px; height: 310px;
    background: var(--card);
    border: 1px solid var(--card-edge);
    border-radius: 22px;
    box-shadow: 0 18px 40px rgba(0,0,0,.55);
    position: relative;
    font-family: "Arimo", Arial, sans-serif;
    color: var(--ink);
  }
  .wordmark {
    font-family: "Arimo", Arial, sans-serif;
    font-weight: 700;
    color: var(--silver);
    text-align: center;
    line-height: 1.05;
  }

  /* Front */
  .card--front { display: flex; align-items: center; }
  .card--front .brand-block {
    width: 220px; height: 100%;
    display: flex; align-items: center; justify-content: center;
    border-right: 1px solid var(--rule);
    margin: 0;
  }
  .card--front .wordmark { font-size: 30px; }
  .details { padding-left: 34px; }
  .person-name {
    font-family: "Courgette", cursive;
    color: var(--gold);
    font-size: 27px;
    line-height: 1.1;
  }
  .person-title { font-size: 15px; margin-top: 2px; }
  .contact-list { list-style: none; margin-top: 28px; font-size: 14.5px; }
  .contact-list li { display: flex; align-items: center; gap: 10px; margin-bottom: 7px; }
  .contact-list svg { width: 15px; height: 15px; flex: none; }
  .accent { color: var(--gold); }

  /* Back */
  .card--back {
    display: flex; flex-direction: column; align-items: center; justify-content: center;
  }
  .card--back .wordmark { font-size: 40px; margin-top: -10px; }
  .tagline {
    margin-top: 42px; font-size: 14.5px; letter-spacing: .1px;
    display: flex; align-items: center; gap: 8px;
  }
  .tagline .dot { width: 6px; height: 6px; border-radius: 50%; background: var(--gold); }
</style>
</head>
<body>
<main class="sheet">

  <section class="card card--front" aria-label="Business card front">
    <div class="brand-block">
      <p class="wordmark">The Loom<br>Briefing</p>
    </div>
    <div class="details">
      <p class="person-name">Belinda Harwick</p>
      <p class="person-title">Director and Stylist</p>
      <ul class="contact-list">
        <li>
          <svg viewBox="0 0 24 24" aria-hidden="true"><path fill="var(--gold)" d="M6.6 10.8a15.1 15.1 0 0 0 6.6 6.6l2.2-2.2c.3-.3.7-.4 1-.2 1.1.4 2.3.6 3.6.6.6 0 1 .4 1 1V20c0 .6-.4 1-1 1A17 17 0 0 1 3 4c0-.6.4-1 1-1h3.5c.6 0 1 .4 1 1 0 1.3.2 2.5.6 3.6.1.3 0 .7-.2 1z"/></svg>
          <span>+61 8 7142 5809</span>
        </li>
        <li>
          <svg viewBox="0 0 24 24" aria-hidden="true"><rect x="2" y="5" width="20" height="14" rx="1" fill="var(--gold)"/><path d="M2.5 5.5 12 13l9.5-7.5" fill="none" stroke="var(--card)" stroke-width="1.6"/></svg>
          <span>belinda@theloombriefing.example</span>
        </li>
        <li>
          <svg viewBox="0 0 24 24" aria-hidden="true"><g fill="none" stroke="var(--gold)" stroke-width="1.8"><circle cx="12" cy="12" r="9.5"/><ellipse cx="12" cy="12" rx="4" ry="9.5"/><path d="M2.5 12h19M4 7h16M4 17h16"/></g></svg>
          <span>www.<span class="accent">theloombriefing</span>.example</span>
        </li>
      </ul>
    </div>
  </section>

  <section class="card card--back" aria-label="Business card back">
    <p class="wordmark">The Loom<br>Briefing</p>
    <p class="tagline">
      <span>Corporate Workwear &amp; Uniform Specialist</span>
      <span class="dot" aria-hidden="true"></span>
      <span>Personal Stylist</span>
    </p>
  </section>

</main>
</body>
</html>
```